Sophisticated, clean website reflecting my feminine, playful side to sell my abstract art,

I need a website no more than 3 pages to showcase my paintings, a little about me and some contact info. I do abstracts so looking for something a little edgy, yet feminine and current.
Updates

Hi there, These are some artists websites that I Iike: Marnelvoss.com (I like how airy it is) peterwallombry.com garethpolvens.com (I like how it scrolls) I'll need a place for a photo ( a headshot-i do not have it yet so I'll need to be able to upload that later) as well as an area for my bio. Also, it's important that I will be able to upload any new photos and descriptions easily so it should be user friendly. Lastly, I like in a sunny place so would like to have this seem upbeat and playful as that is how i like to paint. thanks-I'm trying to upload my photos now -

Target Market(s)

ppl ages 35-70 who want large scale art for their homes

Industry/Entity Type

art

Coding

Coded - Design and coding required

Number of Pages Required

3 page

Colors

Designer to choose colors to be used in the design.

Requirements
Must have
• photos of my art, a place for my bio, be easy to reach me. tasteful-nothing too "in your face" -my clients are pretty high end and organized. They like clean lines
Nice to have
• sophisticated background, muted tones in the back-similar clean font throughout-no cursive
Should not have
• too many dark areas. Too many blocks of color. Too serious.

```html
<!DOCTYPE html>
<html lang="en">
<head>
<meta charset="utf-8">
<title>Maren Holloway — Abstract Paintings</title>
<link rel="stylesheet" href="https://fonts.googleapis.com/css2?family=Montserrat:wght@400;500&family=Quicksand:wght@400;500&display=swap">
<style>
  :root {
    --ink: #111111;
    --text: #3a3a3a;
    --muted: #4a4a4a;
    --gold: #c2b38a;
    --rule: #d9d9d9;
    --paper: #ffffff;
    --hero-a: #c99aa8;
    --hero-b: #8a4632;
    --hero-c: #d9b9b4;
    --gallery-a: #3f8f4e;
    --gallery-b: #e8d3c8;
    --gallery-c: #2e6d6a;
    --portrait: #ececea;
  }
  * { box-sizing: border-box; margin: 0; padding: 0; }
  html, body { width: 1200px; height: 2884px; overflow: hidden; background: var(--paper); }
  body { position: relative; font-family: "Quicksand", sans-serif; color: var(--text); }

  .site-title {
    position: absolute; top: 26px; left: 0; width: 1200px;
    display: flex; justify-content: center; align-items: center; gap: 16px;
    font-family: "Montserrat", sans-serif; font-weight: 400; font-size: 43px;
    color: var(--ink); letter-spacing: 0.5px; line-height: 54px;
  }
  .site-title .mark { width: 40px; height: 40px; background: var(--ink); }
  .header-rule { position: absolute; top: 100px; left: 0; width: 1200px; height: 2px; background: var(--rule); }

  .main-nav { position: absolute; top: 118px; left: 0; width: 1200px; height: 30px; }
  .main-nav a {
    position: absolute; font-family: "Montserrat", sans-serif; font-size: 16px;
    color: var(--muted); text-decoration: none; transform: translateX(-50%); white-space: nowrap;
  }
  .main-nav a.is-active::after {
    content: ""; position: absolute; left: 2px; right: 2px; top: 29px; height: 2px; background: var(--ink);
  }
  .social { display: flex; align-items: center; gap: 6px; }
  .social .dot { width: 32px; height: 32px; border-radius: 50%; background: var(--ink); }

  .hero {
    position: absolute; top: 165px; left: 0; width: 1200px; height: 684px;
    background:
      radial-gradient(circle at 58% 48%, var(--hero-b) 0, rgba(138,70,50,0.3) 18%, transparent 40%),
      radial-gradient(circle at 15% 30%, rgba(138,70,50,0.6) 0, transparent 35%),
      linear-gradient(120deg, var(--hero-c), var(--hero-a) 55%, var(--hero-c));
  }
  .arrow { position: absolute; }

  .portrait-frame { position: absolute; left: 51px; top: 983px; width: 412px; height: 404px; border: 2px solid var(--gold); }
  .portrait { position: absolute; left: 9px; top: 9px; right: 9px; bottom: 9px; background: linear-gradient(180deg, #f2f2f0, var(--portrait)); }

  .section-heading {
    position: absolute; font-family: "Montserrat", sans-serif; font-weight: 400;
    font-size: 40px; color: var(--ink); line-height: 48px; white-space: nowrap;
  }
  .heading-rule { position: absolute; height: 3px; width: 64px; background: var(--gold); }

  .bio { position: absolute; left: 527px; top: 1084px; width: 598px; font-size: 17px; line-height: 27px; color: var(--text); }
  .bio p { text-align: justify; margin-bottom: 14px; }

  .gallery-slide {
    position: absolute; left: 138px; top: 1634px; width: 932px; height: 549px;
    background:
      radial-gradient(circle at 30% 40%, var(--gallery-a) 0, transparent 45%),
      radial-gradient(circle at 80% 50%, var(--gallery-c) 0, transparent 40%),
      radial-gradient(circle at 40% 90%, #b07a2c 0, transparent 30%),
      linear-gradient(110deg, #6aa44a, var(--gallery-b) 50%, #7a5a4a);
  }
  .gallery-slide .inner-frame { position: absolute; left: 16px; top: 14px; right: 16px; bottom: 14px; border: 2px solid rgba(255,255,255,0.85); }

  .contact-intro { position: absolute; top: 2416px; left: 0; width: 1200px; text-align: center; font-size: 16px; color: var(--ink); }
  .contact-line {
    position: absolute; left: 0; width: 1200px; display: flex; justify-content: center; align-items: center; gap: 8px;
    font-size: 25px; color: var(--ink);
  }

  .footer-rule { position: absolute; top: 2776px; left: 0; width: 1200px; height: 2px; background: var(--rule); }
  .site-footer { position: absolute; top: 2810px; left: 0; width: 1200px; height: 30px; font-family: "Montserrat", sans-serif; }
  .site-footer a, .site-footer span {
    position: absolute; font-size: 16px; color: var(--ink); text-decoration: none; white-space: nowrap;
  }
  .site-footer .copyright { font-family: "Quicksand", sans-serif; font-size: 15px; color: var(--muted); }
  .site-footer .social .dot { width: 33px; height: 33px; background: var(--gold); }
</style>
</head>
<body>

<header>
  <div class="site-title"><span class="mark"></span>MAREN HOLLOWAY</div>
  <div class="header-rule"></div>
  <nav class="main-nav">
    <a class="is-active" style="left:210px">HOME</a>
    <a style="left:388px">ABOUT ME</a>
    <a style="left:579px">GALLERY</a>
    <a style="left:767px">CONTACT</a>
    <a class="social" style="left:985px;top:-6px"><span class="dot"></span>@mhollowayart</a>
  </nav>
</header>

<section class="hero" role="img" aria-label="Featured abstract painting in pink, rust and charcoal brushstrokes">
  <svg class="arrow" style="left:18px;top:440px" width="24" height="40" viewBox="0 0 24 40"><polyline points="18,4 6,20 18,36" fill="none" stroke="#fff" stroke-width="5" stroke-linecap="round" stroke-linejoin="round"/></svg>
  <svg class="arrow" style="left:1152px;top:440px" width="24" height="40" viewBox="0 0 24 40"><polyline points="6,4 18,20 6,36" fill="none" stroke="#fff" stroke-width="5" stroke-linecap="round" stroke-linejoin="round"/></svg>
</section>

<section class="about">
  <div class="portrait-frame">
    <div class="portrait" role="img" aria-label="Artist headshot placeholder"></div>
  </div>
  <h2 class="section-heading" style="left:527px;top:994px">ABOUT ME</h2>
  <div class="heading-rule" style="left:527px;top:1051px"></div>
  <div class="bio">
    <p style="text-align:left">Lorem ipsum dolor sit amet, consectetur adipiscing elit, sed do eiusmod tempor incididunt ut labore et dolore magna aliqua. Ut enim ad minim veniam, quis nostrud exercitation</p>
    <p>Duis aute irure dolor in reprehenderit in voluptate velit esse cillum dolore eu fugiat nulla pariatur. Excepteur sint occaecat cupidatat non proident, sunt in culpa qui officia deserunt mollit anim id est laborum.Sed ut perspiciatis unde pariatur. Excepteur sint occaecat cupidatat non proident, sunt in culpa qui officia deserunt mollit anim id est laborum.Sed ut perspiciatioccaecat cupidatat non proident, sunt in culpa qui officia deserunt mollit anim i</p>
  </div>
</section>

<section class="gallery">
  <h2 class="section-heading" style="left:0;width:1192px;text-align:center;top:1528px">PAINTING GALLERY</h2>
  <div class="heading-rule" style="left:570px;top:1582px"></div>
  <div class="gallery-slide" role="img" aria-label="Abstract painting in green, teal and blush brushstrokes">
    <div class="inner-frame"></div>
    <svg class="arrow" style="left:40px;top:245px" width="32" height="60" viewBox="0 0 32 60"><polyline points="28,2 4,30 28,58" fill="none" stroke="#fff" stroke-width="2"/></svg>
    <svg class="arrow" style="left:852px;top:245px" width="32" height="60" viewBox="0 0 32 60"><polyline points="4,2 28,30 4,58" fill="none" stroke="#fff" stroke-width="2"/></svg>
  </div>
</section>

<section class="contact">
  <h2 class="section-heading" style="left:0;width:1200px;text-align:center;top:2336px">CONTACT ME</h2>
  <div class="heading-rule" style="left:554px;top:2390px;width:93px"></div>
  <p class="contact-intro">Please get in touch with me on the below details.</p>
  <div class="contact-line" style="top:2482px">
    <svg width="30" height="30" viewBox="0 0 24 24"><path d="M6.6 2.5l3 3.6-2 2.3c1.3 2.9 3.4 5 6.2 6.3l2.2-2 3.6 2.9-1.6 3.3c-.4.7-1.2 1-2 .8C9.6 17.9 5.9 14.2 4.2 7.8c-.2-.8.1-1.6.8-2z" fill="none" stroke="#333" stroke-width="1.1"/></svg>
    <span>(555) 014 2288</span>
  </div>
  <div class="contact-line" style="top:2541px">
    <svg width="32" height="24" viewBox="0 0 32 24"><rect x="1" y="2" width="30" height="20" fill="none" stroke="#333" stroke-width="1.3"/><polyline points="1,2 16,14 31,2" fill="none" stroke="#333" stroke-width="1.3"/><line x1="1" y1="22" x2="12" y2="11" stroke="#333" stroke-width="1.3"/><line x1="31" y1="22" x2="20" y2="11" stroke="#333" stroke-width="1.3"/></svg>
    <span>marenholloway@info.com</span>
  </div>
</section>

<div class="footer-rule"></div>
<footer class="site-footer">
  <a style="left:124px">ABOUT ME</a>
  <a style="left:268px">GALLERY</a>
  <a style="left:401px">CONTACT</a>
  <span class="copyright" style="left:548px;top:1px">© 2022 Maren Holloway &nbsp; All Rights Reserved</span>
  <a class="social" style="left:954px;top:-4px;display:flex"><span class="dot"></span>@mhollowayart</a>
</footer>

</body>
</html>
```